Deisgn A Manual Cover for an Australian Health Training Company

We are looking for an A4 Front of Manual Cover Design for a comprehensive administrative training manual to be launched soon in Australia.

The title of the book is :

"Drafting, Shaping and Shipping Office Paperwork"

for the Australian Medical Office (smaller font)

Written and compiled by Mel Dobrik

Target Market(s)

25-45 year old medical administrative students (usually female)

Industry/Entity Type

It Company

Font styles to use
Serif

Colors
3176b5
f68d4c
33b8a4
fffbf0

Requirements
Must have
• University like perhaps
• Human element (picture/s of people)
• About the concept of designing and producing documents in a health setting (this can be entirely conceptual).
• Conceptual design would be considered
• Appealing

```html
<!DOCTYPE html>
<html lang="en">
<head>
<meta charset="utf-8">
<title>Drafting, Shaping and Shipping Office Paperwork — Manual Cover</title>
<link rel="stylesheet" href="https://fonts.googleapis.com/css2?family=Bebas+Neue&family=Oswald:wght@500;600&display=swap">
<style>
  :root {
    --stage: #7d9ba8;
    --paper: #fdfdfc;
    --teal: #33b8a4;
    --orange: #f68d4c;
    --blue: #3176b5;
    --grey: #6b6d70;
    --cream: #fffbf0;
    --photo-light: #eef3f8;
    --photo-coat: #dfe8f1;
    --photo-mid: #a9c2d8;
    --photo-deep: #7f9fbf;
    --photo-warm: #e4b99c;
    --photo-hair: #c99a74;
  }
  * { margin: 0; padding: 0; box-sizing: border-box; }
  html, body { width: 1200px; height: 784px; overflow: hidden; }
  body {
    background: radial-gradient(ellipse at 50% 40%, #9db6c1 0%, var(--stage) 70%);
    font-family: "Bebas Neue", "Oswald", sans-serif;
  }
  .cover {
    position: absolute;
    left: 335px; top: 17px;
    width: 530px; height: 750px;
    background: var(--paper);
    overflow: hidden;
    box-shadow: 0 10px 30px rgba(30, 50, 60, 0.25);
  }
  .cover__photo {
    position: absolute;
    left: 0; top: 0;
    width: 470px; height: 750px;
    background:
      radial-gradient(ellipse 85px 70px at 150px 40px, var(--photo-hair) 0%, rgba(201,154,116,0) 100%),
      radial-gradient(ellipse 95px 125px at 150px 150px, var(--photo-warm) 0%, rgba(228,185,156,0) 100%),
      radial-gradient(ellipse 70px 120px at 260px 110px, rgba(228,185,156,0.55) 0%, rgba(228,185,156,0) 100%),
      radial-gradient(ellipse 60px 260px at 50px 480px, var(--photo-deep) 0%, rgba(127,159,191,0) 100%),
      radial-gradient(ellipse 180px 340px at 140px 500px, var(--photo-mid) 0%, rgba(169,194,216,0) 100%),
      radial-gradient(ellipse 130px 300px at 290px 380px, var(--photo-coat) 0%, rgba(223,232,241,0) 100%),
      linear-gradient(180deg, var(--photo-light) 0%, #d6e2ee 55%, var(--photo-light) 100%);
    -webkit-mask-image: linear-gradient(90deg, #000 0%, #000 50%, transparent 100%);
            mask-image: linear-gradient(90deg, #000 0%, #000 50%, transparent 100%);
  }
  .brand {
    position: absolute;
    right: 40px; top: 78px;
    width: 130px;
    text-align: center;
    color: var(--blue);
    font-family: "Oswald", sans-serif;
    font-weight: 500;
    font-size: 9px;
    line-height: 1.25;
    letter-spacing: 0.06em;
    text-transform: uppercase;
  }
  .brand__mark {
    display: block;
    width: 22px; height: 22px;
    margin: 6px auto 0;
    border-radius: 50%;
    background: var(--blue);
  }
  .title {
    position: absolute;
    right: 38px; top: 195px;
    text-align: right;
    font-size: 74px;
    line-height: 0.9;
    letter-spacing: 0.01em;
  }
  .title span { display: block; }
  .title__teal { color: var(--teal); }
  .title__orange { color: var(--orange); }
  .title__blue { color: var(--blue); }
  .title__grey { color: var(--grey); }
  .subtitle {
    position: absolute;
    right: 40px; top: 538px;
    color: var(--blue);
    font-family: "Oswald", sans-serif;
    font-weight: 600;
    font-size: 11px;
    letter-spacing: 0.02em;
  }
  .credit {
    position: absolute;
    right: 40px; top: 640px;
    text-align: right;
  }
  .credit__label {
    color: var(--grey);
    font-family: "Oswald", sans-serif;
    font-weight: 500;
    font-size: 8px;
    letter-spacing: 0.04em;
  }
  .credit__name {
    color: var(--blue);
    font-size: 50px;
    line-height: 1;
    margin-top: 4px;
  }
</style>
</head>
<body>
  <main class="cover">
    <div class="cover__photo" role="img" aria-label="Photograph of a smiling young medical administrator in a white coat with a stethoscope, a colleague behind her"></div>

    <div class="brand">Harbourline College<br>of Training<span class="brand__mark"></span></div>

    <h1 class="title">
      <span class="title__teal">Drafting,</span>
      <span class="title__orange">Shaping</span>
      <span class="title__blue">&amp; Shipping</span>
      <span class="title__grey">Office</span>
      <span class="title__grey">Paperwork</span>
    </h1>
    <p class="subtitle">FOR THE AUSTRALIAN MEDICAL OFFICE</p>

    <div class="credit">
      <p class="credit__label">WRITTEN AND COMPILED BY</p>
      <p class="credit__name">MEL DOBRIK</p>
    </div>
  </main>
</body>
</html>
```